Construction company that specializes in roofing and siding

https://maplecrestbuild.example/featured-projects/

https://www.bramwickhomesllc.example/#

https://www.tallgrovecontractors.example/residential-siding-services/

Please model a website after these examples
I posted a doc that has some content to get you started. I will upload more content and photos as the site progresses.

Coded - Design and coding required

5+ page

```html
<!DOCTYPE html>
<html lang="en">
<head>
<meta charset="utf-8">
<title>Stonecrest Construction</title>
<link href="https://fonts.googleapis.com/css2?family=Poppins:ital,wght@0,300;0,400;0,500;0,600;0,700;0,800;1,300&display=swap" rel="stylesheet">
<style>
:root{
  --ink:#1f1f1f;
  --dark:#232323;
  --mid:#8a8a8a;
  --soft:#d9d9d9;
  --pale:#f3f3f3;
  --text:#6d6d6d;
  --white:#ffffff;
}
*{margin:0;padding:0;box-sizing:border-box}
html,body{width:1200px;height:4946px;overflow:hidden;background:var(--white)}
body{font-family:'Poppins',sans-serif;color:var(--ink)}
.page{position:relative;width:1200px;height:4946px;overflow:hidden}
.abs{position:absolute}
svg.band{position:absolute;left:0;width:1200px;display:block}

/* header */
.site-header{top:0;left:0;width:1200px;height:73px;background:var(--white);box-shadow:0 1px 4px rgba(0,0,0,.08);z-index:5}
.brand{position:absolute;left:88px;top:22px;display:flex;align-items:center;gap:10px;font-weight:700;font-size:17px;letter-spacing:1px;color:#444}
.brand .mark{width:24px;height:24px;background:#444}
.main-nav{position:absolute;top:0;left:300px;height:73px;display:flex;align-items:center}
.main-nav a{position:absolute;font-size:11px;font-weight:600;color:#333;text-decoration:none;white-space:nowrap}
.header-divider{position:absolute;left:958px;top:26px;width:1px;height:22px;background:#999}
.header-social{position:absolute;left:986px;top:28px;display:flex;gap:9px}
.header-social span{width:24px;height:24px;border-radius:50%;background:#8a8a8a;display:flex;align-items:center;justify-content:center}

/* hero */
.hero{top:73px;left:0;width:1200px;height:705px}
.hero-photo{position:absolute;inset:0;background:linear-gradient(100deg,#5f6266 0%,#8d8f92 45%,#b9a88f 75%,#d8c7a8 100%)}
.hero-photo::after{content:"";position:absolute;inset:0;background:linear-gradient(90deg,rgba(30,30,30,.55),rgba(30,30,30,0) 60%)}
.hero-title{position:absolute;left:85px;top:225px;font-size:70px;line-height:72px;font-weight:700;color:var(--white)}
.hero-text{position:absolute;left:86px;top:386px;width:490px;font-size:13px;line-height:23px;color:var(--white)}
.btn-dark{position:absolute;background:var(--dark);color:var(--white);font-size:13px;font-weight:600;border-radius:5px;display:flex;align-items:center;justify-content:center;gap:10px}
.slider-arrow{position:absolute;width:32px;height:60px;background:rgba(255,255,255,.15);color:#ddd;font-size:14px;display:flex;align-items:center;justify-content:center}

.quote-card{top:330px;left:806px;width:304px;height:432px;background:var(--mid);border-radius:4px;overflow:hidden;z-index:3;box-shadow:0 4px 14px rgba(0,0,0,.15)}
.quote-head{height:103px;background:var(--white);margin:0 0 0 0;position:relative}
.quote-head h3{position:absolute;left:30px;top:28px;font-size:17px;line-height:22px;font-weight:700;color:var(--ink)}
.quote-head .seal{position:absolute;right:26px;top:22px;width:60px;height:60px;border-radius:50%;background:#555}
.field{position:absolute;left:33px;width:242px;height:31px;background:var(--white);border-radius:4px;font-size:9px;color:#aaa;padding:9px 12px}

/* about */
.shield-photo{position:absolute}
.section-title{position:absolute;font-weight:700;color:var(--ink)}
.body-copy{position:absolute;font-size:13px;line-height:22px;color:var(--text)}

/* services */
.service{position:absolute;width:284px;height:304px}
.service svg{position:absolute;inset:0}
.service .icon{position:absolute;left:82px;top:40px;width:120px;height:110px;border-radius:8px;background:#e2e2e2}
.service h4{position:absolute;left:0;right:0;top:168px;text-align:center;font-size:21px;font-weight:600;color:var(--ink)}
.service.feature h4{top:148px;color:var(--white)}
.service.feature p{position:absolute;left:60px;right:60px;top:180px;text-align:center;font-size:13px;line-height:22px;color:#e8e8e8}
.service.feature .icon{background:rgba(255,255,255,.25);height:70px;top:60px}

/* reviews */
.quote-mark{position:absolute;left:628px;top:2620px;font-size:120px;line-height:120px;font-weight:800;color:#555}
.review-text{position:absolute;left:630px;top:2696px;width:470px;font-size:23px;line-height:31px;font-style:italic;font-weight:300;color:#7a7a7a}
.signature{position:absolute;left:628px;top:2880px;width:190px;height:42px;border-radius:4px;background:linear-gradient(90deg,#e6e6e6,#f4f4f4)}

/* cta */
.cta-title{position:absolute;left:0;width:1200px;top:3292px;text-align:center;font-size:48px;line-height:84px;font-weight:700;color:var(--white)}
.cta-line{position:absolute;left:0;width:1200px;top:3446px;text-align:center;font-size:13px;color:var(--white)}
.btn-light{position:absolute;left:494px;top:3494px;width:212px;height:40px;background:var(--white);border-radius:5px;font-size:13px;font-weight:600;color:var(--ink);display:flex;align-items:center;justify-content:center}

/* contact */
.contact-heading{position:absolute;top:3808px;font-size:26px;font-weight:400;color:var(--ink)}
.contact-card{position:absolute;left:194px;top:3863px;width:326px;height:323px;background:var(--pale);border-radius:6px}
.contact-item{position:absolute;left:48px;font-size:13px;line-height:22px;color:var(--text)}
.contact-item strong{display:block;color:var(--ink);font-weight:600}
.contact-item svg{position:absolute;left:-24px;top:4px}
.map-area{position:absolute;left:563px;top:3863px;width:445px;height:323px;background:linear-gradient(135deg,#e9ece8,#d9e3d6 60%,#e6e8ec)}

/* footer */
.footer-brand{position:absolute;left:225px;top:4520px;display:flex;align-items:center;gap:16px;font-size:40px;font-weight:700;letter-spacing:3px;color:var(--white)}
.footer-brand .mark{width:72px;height:72px;border:6px solid var(--white)}
.footer-social{position:absolute;left:312px;top:4612px;display:flex;gap:15px}
.footer-social span{width:43px;height:43px;border-radius:50%;background:#8a8a8a;display:flex;align-items:center;justify-content:center}
.footer-col h5{font-size:21px;font-weight:500;color:var(--white);padding-bottom:10px;border-bottom:1px solid #777;display:inline-block}
.footer-col ul{list-style:none;margin-top:10px}
.footer-col li{font-size:10px;line-height:26px;color:#ddd}
.bottom-nav{position:absolute;top:4764px;left:156px;width:888px;display:flex;justify-content:space-between;font-size:16px;font-weight:600;color:var(--white)}
.copyright{position:absolute;left:0;width:1200px;top:4882px;text-align:center;font-size:15px;color:#e5e5e5}
.to-top{position:absolute;left:1112px;top:4824px;width:40px;height:40px;border-radius:50%;background:#6c6c6c;display:flex;align-items:center;justify-content:center}
</style>
</head>
<body>
<div class="page">

  <!-- header -->
  <header class="site-header abs">
    <div class="brand"><span class="mark"></span>STONECREST</div>
    <nav class="main-nav">
      <a style="left:5px;top:30px"><svg width="14" height="12" viewBox="0 0 14 12"><path d="M7 0 0 6h2v6h4V8h2v4h4V6h2z" fill="#888"/></svg></a>
      <a style="left:57px;top:33px">ROOFING ⌄</a>
      <a style="left:142px;top:33px">SIDING ⌄</a>
      <a style="left:215px;top:33px">GUTTERS</a>
      <a style="left:299px;top:33px">WINDOWS</a>
      <a style="left:393px;top:33px">REPAIR ⌄</a>
      <a style="left:464px;top:33px">STORM DAMAGE REPAIR ⌄</a>
    </nav>
    <div class="header-divider"></div>
    <div class="header-social">
      <span></span><span></span>
      <span><svg width="11" height="11" viewBox="0 0 12 12"><circle cx="5" cy="5" r="3.6" fill="none" stroke="#fff" stroke-width="1.6"/><path d="M7.7 7.7 11 11" stroke="#fff" stroke-width="1.8"/></svg></span>
      <span></span>
    </div>
  </header>

  <!-- hero -->
  <section class="hero abs">
    <div class="hero-photo" role="img" aria-label="Roofer installing shingles on a house roof beside a brick chimney"></div>
    <h1 class="hero-title">Stonecrest<br>Construction</h1>
    <p class="hero-text">You deserve timely service, high quality materials, expert installation, and an stonecrest warranty. That is what we promise to deliver. I invite you to put us to the test today.</p>
    <div class="btn-dark" style="left:85px;top:496px;width:135px;height:38px">Contact Us</div>
    <div class="slider-arrow" style="left:27px;top:250px">‹</div>
    <div class="slider-arrow" style="left:1137px;top:250px">›</div>
  </section>
  <svg class="band" style="top:560px;height:220px" viewBox="0 0 1200 220">
    <polygon points="0,80 650,148 0,220" fill="#8a8a8a"/>
    <polygon points="0,218 1200,70 1200,220 0,220" fill="#fff"/>
  </svg>

  <div class="quote-card abs">
    <div class="quote-head">
      <h3>START YOUR FREE<br>QUOTE</h3>
      <div class="seal"></div>
    </div>
    <div class="field" style="top:137px">Name *</div>
    <div class="field" style="top:178px">Email*</div>
    <div class="field" style="top:219px">Phone*</div>
    <div class="field" style="top:259px;height:81px">Write message here...</div>
    <div class="btn-dark" style="left:85px;top:367px;width:134px;height:39px">subscribe
      <svg width="12" height="12" viewBox="0 0 12 12"><path d="M0 5 12 0 8 12 6 7z" fill="#fff"/></svg></div>
  </div>

  <!-- about -->
  <svg class="shield-photo" style="left:88px;top:854px" width="469" height="513" viewBox="0 0 469 513" role="img" aria-label="Roofer in a yellow hard hat and safety vest fitting roof tiles">
    <defs><linearGradient id="aboutTone" x1="0" y1="0" x2="1" y2="1"><stop offset="0" stop-color="#9aa0a6"/><stop offset=".5" stop-color="#b9c05a"/><stop offset="1" stop-color="#7d8288"/></linearGradient></defs>
    <path d="M234 0 469 110 469 300 Q469 420 234 513 Q0 420 0 300 L0 110Z" fill="url(#aboutTone)"/>
  </svg>
  <h2 class="section-title" style="left:634px;top:870px;font-size:49px">About</h2>
  <p class="abs" style="left:635px;top:938px;font-size:13px;font-weight:600;color:var(--ink)">From humble beginnings:</p>
  <p class="body-copy" style="left:635px;top:970px;width:480px">In 2016 Dale Harper started helping people with their home improvement projects. His very first job was installing window trim for a wonderful homeowner in Pine Hollow MN. He did his best work and made sure he treated his first customer like family. Afterall, his first customer was Maria Harper, his Mom.</p>
  <p class="body-copy" style="left:635px;top:1100px;width:480px">Today, Dale and the Stonecrest Construction team are helping homeowners around Minnesota; carrying the spirit of his first job onto every job they touch.</p>
  <div class="btn-dark" style="left:635px;top:1194px;width:134px;height:41px">Learn More</div>

  <!-- services -->
  <svg class="band" style="top:1375px;height:1120px" viewBox="0 0 1200 1120">
    <polygon points="235,155 1200,5 1200,30 235,180" fill="#dedede"/>
    <polygon points="640,190 1200,40 1200,190" fill="#8a8a8a"/>
    <polygon points="0,190 1200,65 1200,935 0,935" fill="#232323"/>
    <rect x="0" y="185" width="1200" height="760" fill="#232323"/>
    <polygon points="0,955 700,1035 0,1080" fill="#8a8a8a"/>
    <polygon points="0,1085 990,935 990,955 0,1110" fill="#dedede"/>
    <polygon points="0,1110 1200,930 1200,1120 0,1120" fill="#fff"/>
  </svg>

  <div class="service" style="left:144px;top:1624px">
    <svg viewBox="0 0 284 304" width="284" height="304"><path d="M142 0 284 52 284 165 Q284 250 142 304 Q0 250 0 165 L0 52Z" fill="#fff"/></svg>
    <div class="icon" role="img" aria-label="Roof tiles icon"></div>
    <h4>ROOFING</h4>
  </div>
  <div class="service feature" style="left:457px;top:1624px">
    <svg viewBox="0 0 284 304" width="284" height="304"><defs><linearGradient id="featTone" x1="0" y1="0" x2="1" y2="1"><stop offset="0" stop-color="#3a3a3a"/><stop offset="1" stop-color="#a9a9a9"/></linearGradient></defs><path d="M142 0 284 52 284 165 Q284 250 142 304 Q0 250 0 165 L0 52Z" fill="url(#featTone)"/></svg>
    <div class="icon" role="img" aria-label="Car outline icon"></div>
    <h4>SIDING</h4>
    <p>Architectural shingles are the most cost effective choice in</p>
  </div>
  <div class="service" style="left:772px;top:1624px">
    <svg viewBox="0 0 284 304" width="284" height="304"><path d="M142 0 284 52 284 165 Q284 250 142 304 Q0 250 0 165 L0 52Z" fill="#fff"/></svg>
    <div class="icon" role="img" aria-label="Gutter downspout icon"></div>
    <h4>GUTTERS</h4>
  </div>
  <div class="service" style="left:298px;top:1920px">
    <svg viewBox="0 0 284 304" width="284" height="304"><path d="M142 0 284 52 284 165 Q284 250 142 304 Q0 250 0 165 L0 52Z" fill="#fff"/></svg>
    <div class="icon" role="img" aria-label="Window installation icon"></div>
    <h4>WINDOWS</h4>
  </div>
  <div class="service" style="left:620px;top:1920px">
    <svg viewBox="0 0 284 304" width="284" height="304"><path d="M142 0 284 52 284 165 Q284 250 142 304 Q0 250 0 165 L0 52Z" fill="#fff"/></svg>
    <div class="icon" role="img" aria-label="Mechanic repair icon"></div>
    <h4>REPAIR</h4>
  </div>

  <!-- reviews -->
  <svg class="shield-photo" style="left:90px;top:2544px" width="467" height="499" viewBox="0 0 467 499" role="img" aria-label="Worker in hard hat and safety vest installing solar panels">
    <defs><linearGradient id="reviewTone" x1="0" y1="0" x2="1" y2="1"><stop offset="0" stop-color="#a7b3c4"/><stop offset=".5" stop-color="#c9d35a"/><stop offset="1" stop-color="#5c6a80"/></linearGradient></defs>
    <path d="M233 0 467 100 467 290 Q467 410 233 499 Q0 410 0 290 L0 100Z" fill="url(#reviewTone)"/>
  </svg>
  <h2 class="section-title" style="left:628px;top:2552px;font-size:42px">CUSTOMERS REVIEWS</h2>
  <div class="quote-mark">“</div>
  <p class="review-text">You deserve timely service, high quality materials, expert installation, and an stonecrest warranty. That is what we promise to deliver. I invite you to put us to the test today. Sincerely,</p>
  <div class="signature" role="img" aria-label="Handwritten signature of Dale Harper"></div>
  <p class="abs" style="left:629px;top:2932px;font-size:13px;font-weight:500;color:var(--ink)">Owner Stonecrest</p>

  <!-- consultation -->
  <svg class="band" style="top:3035px;height:715px" viewBox="0 0 1200 715">
    <polygon points="235,130 1200,0 1200,28 235,155" fill="#dedede"/>
    <polygon points="700,191 1200,55 1200,191" fill="#8a8a8a"/>
    <polygon points="0,191 1200,80 1200,560 0,560" fill="#232323"/>
    <rect x="0" y="188" width="1200" height="400" fill="#232323"/>
    <polygon points="0,555 630,600 0,670" fill="#8a8a8a"/>
    <polygon points="0,680 997,575 997,592 0,702" fill="#dedede"/>
    <polygon points="0,702 1200,570 1200,715 0,715" fill="#fff"/>
  </svg>
  <h2 class="cta-title">FREE CONSULTATION WITH<br>EXCEPTIONAL QUALITY</h2>
  <p class="cta-line">Just one call away: +1 555 014 2703</p>
  <div class="btn-light">Get your consultation</div>

  <!-- contact -->
  <h3 class="contact-heading" style="left:202px">Get In Touch</h3>
  <h3 class="contact-heading" style="left:563px">Our Location</h3>
  <div class="contact-card">
    <div class="contact-item" style="top:37px">
      <svg width="12" height="10" viewBox="0 0 12 10"><rect width="12" height="10" rx="1" fill="#555"/><path d="M0 1 6 6 12 1" stroke="#fff" fill="none"/></svg>
      <strong>Email:</strong>info@stonecrestbuild.example</div>
    <div class="contact-item" style="top:98px">
      <svg width="12" height="12" viewBox="0 0 12 12"><path d="M2 0h3l1 3-2 1.5a7 7 0 0 0 3.5 3.5L9 6l3 1v3a2 2 0 0 1-2 2C4.5 12 0 7.5 0 2a2 2 0 0 1 2-2z" fill="#555"/></svg>
      <strong>Phone:</strong>+1 555 010 7890</div>
    <div class="contact-item" style="top:161px">
      <svg width="10" height="13" viewBox="0 0 10 13"><path d="M5 0a5 5 0 0 1 5 5c0 3.5-5 8-5 8S0 8.5 0 5a5 5 0 0 1 5-5z" fill="#555"/><circle cx="5" cy="5" r="1.8" fill="#f3f3f3"/></svg>
      <strong>Address</strong>line come here, Lorem<br>ipsum, 123 456.</div>
    <div class="btn-dark" style="left:72px;top:253px;width:134px;height:39px">Contact Us</div>
  </div>
  <div class="map-area" role="img" aria-label="Street map showing the office location"></div>

  <!-- footer -->
  <svg class="band" style="top:4240px;height:706px" viewBox="0 0 1200 706">
    <polygon points="235,145 1200,0 1200,28 235,170" fill="#dedede"/>
    <polygon points="750,205 1200,60 1200,205" fill="#8a8a8a"/>
    <polygon points="0,205 1200,85 1200,706 0,706" fill="#232323"/>
  </svg>
  <div class="footer-brand"><span class="mark"></span>STONECREST</div>
  <div class="footer-social">
    <span></span><span></span>
    <span><svg width="17" height="17" viewBox="0 0 12 12"><circle cx="5" cy="5" r="3.6" fill="none" stroke="#fff" stroke-width="1.5"/><path d="M7.7 7.7 11 11" stroke="#fff" stroke-width="1.7"/></svg></span>
    <span></span>
  </div>
  <div class="footer-col abs" style="left:657px;top:4500px">
    <h5>STONECREST</h5>
    <ul><li>See us in Action</li><li>FAQ</li><li>Test Videos</li><li>Video Gallery</li></ul>
  </div>
  <div class="footer-col abs" style="left:887px;top:4500px">
    <h5>COMPANY</h5>
    <ul><li>About</li><li>Reviews</li><li>Contact</li></ul>
  </div>
  <nav class="bottom-nav"><span>HOME</span><span>ROOFING</span><span>SIDING</span><span>GUTTERS</span><span>WINDOWS</span><span>REPAIR</span><span>STORM DAMAGE REPAIR</span></nav>
  <div class="to-top"><svg width="12" height="14" viewBox="0 0 12 14"><path d="M6 13V2M1 6l5-5 5 5" stroke="#fff" stroke-width="1.6" fill="none"/></svg></div>
  <p class="copyright">COPYRIGHT © 2024 STONECREST | ALL RIGHTS RESERVED.</p>

</div>
</body>
</html>
```